New, modern business card for growing audiology practice

We need a new business card for our audiology practice. Our logo and website have recently changed (more modern) and we want our business cards to reflect this change.
We conduct hearing tests, perform earwax removals, and fit & dispense hearing aids to our patients. We are a family owned practice in which the owner is the one who works directly with the patient. I have attached logos in various formats to use, as well as two ideas I found on this website; as well as a scanned copy of our current logo. Good luck!

Industry/Entity Type

Business

Contact Information for Business Card

Company name: Tolvera Hearing Center
Provider name: Peter Wolstenby, Au.D. F/NSB
Phone number: (440) 683-5127
Address: 837 W. Lindell Ave. Brookmere Falls, OH 44391
email: tolverahearing@postvane.com
website: tolverahearing.com

Colors
000000
aaaaaa
dbdbdb
cacaca
9bcb3c
afd23c
cadf82
b1b1b1

Requirements
Must have
• My card must include information in the "details" section. In the attached images, I found a few that I liked and I would like to model after - "brisky bouncin'" and "Sound Method Center".
• Must be horizontal.
• Must include logos provided. I uploaded them in various file formats and various ways.
• Must match logo font, if possible, if not, please get as close as you can.
Nice to have
• I really like the idea of having a color on one side with just the logo and company name and the contact information and provider name on the other side. I also really like the idea of having the main color dominating on the logo/company side with accent of that same color on the contact side of the card.
Should not have
• Must not be vertical.

```html
<!DOCTYPE html>
<html lang="en">
<head>
<meta charset="utf-8">
<title>Tolvera Hearing Center – Business Card</title>
<link rel="stylesheet" href="https://fonts.googleapis.com/css2?family=Roboto:wght@400;500&family=Roboto+Condensed:wght@700&family=Lato:wght@400&display=swap">
<style>
  :root {
    --backdrop: #d3a87e;
    --card-dark: #1b1c1e;
    --card-light: #f4f4f3;
    --brand-green: #74a33a;
    --ink: #1a1a1a;
    --ink-soft: #555555;
    --web-white: #f2f2f2;
  }
  * { margin: 0; padding: 0; box-sizing: border-box; }
  html, body {
    width: 1200px; height: 960px; overflow: hidden;
    background: var(--backdrop);
  }
  .canvas { position: relative; width: 1200px; height: 960px; }

  .card { position: absolute; width: 602px; height: 344px; }

  /* Front side */
  .card-front {
    left: 322px; top: 108px;
    background: var(--card-dark);
    border-radius: 18px;
  }
  .front-name {
    position: absolute; left: 0; right: 0; top: 150px;
    text-align: center;
    font-family: "Lato", sans-serif; font-weight: 400;
    font-size: 34px; letter-spacing: 1px;
    color: var(--brand-green);
  }
  .front-web {
    position: absolute; left: 0; right: 0; top: 293px;
    text-align: center;
    font-family: "Roboto", sans-serif; font-size: 14px;
    letter-spacing: 3.2px; color: var(--web-white);
  }

  /* Back side */
  .card-back {
    left: 320px; top: 493px; width: 600px; height: 342px;
    background: var(--card-light);
    border-radius: 16px;
  }
  .brand-lockup {
    position: absolute; right: 32px; top: 42px;
    display: flex; align-items: center; gap: 10px;
  }
  .brand-dot {
    width: 16px; height: 16px; border-radius: 50%;
    background: var(--brand-green);
  }
  .brand-name {
    font-family: "Lato", sans-serif; font-weight: 400;
    font-size: 21px; color: var(--ink); letter-spacing: 0.2px;
  }
  .provider { position: absolute; left: 39px; top: 188px; }
  .provider-name {
    font-family: "Roboto Condensed", sans-serif; font-weight: 700;
    font-size: 21px; color: var(--brand-green); line-height: 1.1;
  }
  .provider-title {
    font-family: "Roboto", sans-serif; font-weight: 500;
    font-size: 14px; color: var(--ink); margin-top: 5px;
  }
  .contact-list {
    position: absolute; left: 40px; top: 251px;
    list-style: none;
    font-family: "Roboto", sans-serif; font-size: 14px; color: var(--ink-soft);
  }
  .contact-list li { display: flex; align-items: center; height: 19.5px; gap: 9px; }
  .contact-list svg { width: 13px; height: 13px; fill: var(--brand-green); flex: none; }
  .address {
    position: absolute; left: 274px; top: 271px;
    font-family: "Roboto", sans-serif; font-size: 14px; color: var(--ink-soft);
    line-height: 19.5px; font-style: normal;
  }
</style>
</head>
<body>
<main class="canvas">
  <section class="card card-front">
    <div class="front-name">Tolvera Hearing Center</div>
    <div class="front-web">www.tolverahearing.com</div>
  </section>

  <section class="card card-back">
    <div class="brand-lockup">
      <span class="brand-dot"></span>
      <span class="brand-name">TOLVERA HEARING CENTER</span>
    </div>

    <div class="provider">
      <div class="provider-name">PETER WOLSTENBY</div>
      <div class="provider-title">AU.D. F/NSB</div>
    </div>

    <ul class="contact-list">
      <li>
        <svg viewBox="0 0 16 16" aria-hidden="true"><path d="M3.6 1.2l2.3 2.6c.4.4.4 1 0 1.4L4.7 6.4c.9 2 2.6 3.8 4.9 4.9l1.2-1.2c.4-.4 1-.4 1.4 0l2.6 2.3c.4.4.4 1 0 1.4l-1.3 1.3C11.4 16.1 0 7.8 1 2.4L2.2 1.2c.4-.4 1-.4 1.4 0z"/></svg>
        (440) 683-5127
      </li>
      <li>
        <svg viewBox="0 0 16 16" aria-hidden="true"><path d="M1 3h14v1.2L8 8.6 1 4.2z"/><path d="M1 5.8l7 4.4 7-4.4V13H1z"/></svg>
        tolverahearing@postvane.com
      </li>
      <li>
        <svg viewBox="0 0 16 16" aria-hidden="true"><circle cx="8" cy="8" r="7"/><path d="M1.5 8h13M8 1.2c-2.4 2.2-2.4 11.4 0 13.6M8 1.2c2.4 2.2 2.4 11.4 0 13.6" stroke="#f4f4f3" stroke-width="1.2" fill="none"/></svg>
        tolverahearing.com
      </li>
    </ul>

    <address class="address">
      837 W. Lindell Ave.<br>
      Brookmere Falls, OH 44391
    </address>
  </section>
</main>
</body>
</html>
```